Brightmoor Hall Lead Generator + Checklist

I have typed up a 9 page word doc to be a lead generator for my website called "7 Quiet Slip-Ups Party Hosts Overlook" and I am looking for someone to clean it up, and make it professional and inline with our brand.

Logo Hex: #971F20

Industry/Entity Type

Event Planning

Font styles to use
Other font styles liked:
• Helvetica Neue is our brands font, but it doesn't have to be that. Something similar that is rounded would be good like Arial I think.

Requirements
Must have
• Clean, but elegant design.
• Because it is very text heavy, have the topics easily broken out and maybe staggered so that it is easy to identify main topics and sub topics.
Should not have
• Not just looking for basic formating around the edges of the document, but to also have the text displayed in an easily readable way with clear sections.

```html
<!DOCTYPE html>
<html lang="en">
<head>
<meta charset="utf-8">
<title>Brightmoor Hall – Guide Spread</title>
<link href="https://fonts.googleapis.com/css2?family=Arimo:ital,wght@0,400;0,700;1,700&display=swap" rel="stylesheet">
<style>
  :root {
    --brand-red: #971f20;
    --ink: #1c1c1c;
    --numeral: #e9e9ea;
    --paper: #ffffff;
  }
  * { box-sizing: border-box; margin: 0; padding: 0; }
  html, body { width: 1200px; height: 777px; overflow: hidden; background: var(--paper); }
  body { font-family: "Arimo", Arial, sans-serif; color: var(--ink); position: relative; }

  .page { position: absolute; top: 0; width: 600px; height: 777px; overflow: hidden; }
  .page--left { left: 0; }
  .page--right { left: 600px; }

  .page-numeral {
    position: absolute; font-size: 300px; line-height: 1; font-weight: 400;
    color: var(--numeral); z-index: 0; top: 548px;
  }
  .page--left .page-numeral { left: 30px; }
  .page--right .page-numeral { left: 32px; }

  .section-band {
    position: absolute; top: 56px; height: 18px; width: 524px;
    background: var(--brand-red); color: #fff; font-weight: 700; font-size: 14px;
    line-height: 18px; display: flex; z-index: 1;
  }
  .page--left .section-band { left: 34px; }
  .page--right .section-band { left: 42px; }
  .section-band .num { width: 36px; padding-left: 4px; }

  .section-body { position: absolute; top: 87px; z-index: 1; font-size: 11.2px; line-height: 13.5px; }
  .page--left .section-body { left: 70px; width: 490px; }
  .page--right .section-body { left: 79px; width: 488px; }

  .item { display: grid; grid-template-columns: var(--label, 19px) 1fr; margin-bottom: 5px; }
  .item > .label { font-weight: 700; }
  .item.roman > .label { font-weight: 400; }
  .sub { margin-left: 47px; --label: 22px; margin-top: 5px; }
  .subsub { margin-left: 35px; --label: 16px; margin-top: 5px; }
  .page--right .sub { margin-left: 22px; --label: 29px; }
  .item.roman-bold > .label { font-weight: 700; text-align: right; padding-right: 9px; }
  .page--right .item.tight { margin-left: 15px; }
  b { font-weight: 700; }

  .folio { position: absolute; top: 741px; font-size: 7.4px; z-index: 1; }
  .folio strong { color: var(--brand-red); }
  .page--left .folio { left: 34px; }
  .page--right .folio { right: 34px; }

  .corner { position: absolute; bottom: 0; z-index: 1; }
  .page--left .corner { left: 0; }
  .page--right .corner { right: 0; }
</style>
</head>
<body>

<section class="page page--left">
  <div class="page-numeral" aria-hidden="true">2</div>
  <h2 class="section-band"><span class="num">2.</span><span>Know your audience</span></h2>

  <div class="section-body">
    <div class="item"><span class="label">a.</span><div>What <b>feel</b> are they looking for?
      <div class="sub">
        <div class="item roman"><span class="label">i.</span><div>The first event I ever planned was for 100 people for my Army unit and my boss had just been switched out. I made the (false) assumption that my new boss would like the same venue that my previous boss did - and I couldn't have been more wrong.</div></div>
        <div class="item roman"><span class="label">ii.</span><div>Although I had done everything “right”, the venue was much more casual than what he had wanted and since it was the first time he was speaking to most of the units leaders at once, along with their spouses, he was not happy.</div></div>
        <div class="item roman"><span class="label">iii.</span><div>So this is why after knowing your event, make sure you know your audience: your boss, board and/or attendees expectations for the event.
          <div class="subsub">
            <div class="item roman"><span class="label">1.</span><div>Are they looking to make a splash that they hope will propel the organization to the next level or are they looking for a practical venue for a recurring event?</div></div>
            <div class="item roman"><span class="label">2.</span><div>Are they looking for an upscale venue where the price is secondary or are they on a tight budget and looking to get a good value?</div></div>
            <div class="item roman"><span class="label">3.</span><div>Clarifying these expectations upfront will ensure that you only spend time looking at venues that are a good fit, as opposed to wasting time looking at venues that aren't.</div></div>
          </div>
        </div></div>
      </div>
    </div></div>

    <div class="item"><span class="label">b.</span><div><b>How many people</b> are expected to come?
      <div class="sub" style="margin-top:0">
        <div class="item roman"><span class="label">i.</span><div>Headcounts are always tricky, but starting to look at venues without a clear picture of how many guests will be coming, will also lead you to waste valuable time looking at the wrong size venues.</div></div>
        <div class="item roman"><span class="label">ii.</span><div>Right or wrong, people judge an event on how well it fills a room. If the room is half full, people will question if it is even worth being there. But, if a room is so small that people can't get it in - they won't stick around for long. So finding the perfect sized room is key, but that can't be done without an accurate headcount.</div></div>
        <div class="item roman"><span class="label">iii.</span><div>Here are some ideas to get an accurate headcount (especially if this is a first time or infrequent event).
          <div class="subsub">
            <div class="item roman"><span class="label">1.</span><div>Attempt to find information about the number of attendees for previous similar events.</div></div>
            <div class="item roman"><span class="label">2.</span><div>Contact people who previously planned the event if this is your first time.</div></div>
            <div class="item roman"><span class="label">3.</span><div>Survey a few people who may be going to see if there is maybe another conflict that will be pulling potential guests away from the event.</div></div>
            <div class="item roman"><span class="label">4.</span><div>You can also create a Gatherly Event, send out a simple FormNest Form or send RSVP emails using programs like InviteLoom to send out to your guests to help get a good headcount as well.</div></div>
          </div>
        </div></div>
      </div>
    </div></div>

    <div class="item"><span class="label">c.</span><div>Now that you have a good feel for the type of event and the headcount the fun part can begin - you can start looking for a venue. By knowing this information up front, you'll save yourself the time of going through the process of booking a venue - only to find out that it isn't the right feel or the right size.</div></div>
  </div>

  <p class="folio"><strong>4</strong> | Brightmoor Hall</p>
  <svg class="corner" width="40" height="60" viewBox="0 0 40 60" aria-hidden="true">
    <path d="M0 12 Q22 18 28 60 L0 60 Z" fill="var(--brand-red)"/>
  </svg>
</section>

<section class="page page--right">
  <div class="page-numeral" aria-hidden="true">3</div>
  <h2 class="section-band"><span class="num">3.</span><span>Ask the venue the <i>right</i> questions.</span></h2>

  <div class="section-body">
    <div class="item"><span class="label">a.</span><div>Now that you're at a good starting point, it doesn't take long to realize that's only half the battle when planning an event. The next challenge is finding a venue. Unfortunately, many venues for mid-size venues for 20-200 people such as restaurants, have limited information on their website. Attempting to call or email a venue is always a mixed bag, some will get back to you soon, others may take days and some you may never hear back from.
      <div class="sub">
        <div class="item roman-bold"><span class="label">i.</span><div><b>Getting Started -</b> Instead of trying to chase down basic information on venues websites and by contacting them, an easy way to start your search is to use our website which will help you quickly eliminate venues that don't meet the basic criteria. You can then save the venues you like, and lastly compare a few that you think would be perfect for your event.</div></div>
        <div class="item roman-bold"><span class="label">ii.</span><div><b>360 Tours -</b> One feature that many people find helpful in finding a venue that meets their needs is using the 360 Tour feature on our website that are found at the bottom of most venues pages. The 360 Tours also make it easy for you to give your boss a tour of the venue without even leaving the office.</div></div>
        <div class="item roman-bold"><span class="label">iii.</span><div><b>Tech Support</b> - Make sure to check to see if the venue has the tech support and amenities you need, or come up with a plan to provide them internally. It is also good to know how much tech support will cost early in the decision making process, because that is a key area where costs can creep up on you.</div></div>
        <div class="item roman-bold"><span class="label">iv.</span><div><b>Confirm Fees -</b> Now that you have a few venues in mind, you want to confirm important details like what fees, charges and taxes will apply to get a better picture of the total cost. This can be done by viewing menus and policies that are attached at the bottom of each venue's page and then messaging the venues to clarify any remaining questions.</div></div>
        <div class="item roman-bold"><span class="label">v.</span><div><b>Refund Policies -</b> Clarify upfront when and if there is a deposit due, when payments are due and what the cancellation policy is. This will save you a lot of heartache if there is bad weather, or something unexpected happens with your group and you have to negotiate a refund, where if you know up front there won't be any questions.</div></div>
        <div class="item roman-bold"><span class="label">vi.</span><div><b>Parking -</b> This is one of those classic ankle-biter issues that can be frustrating. Make sure to get a good idea from the venue on what parking options will be available, if the venue provides complimentary parking for events, and how the day of week and time of day will affect available parking during the event.</div></div>
        <div class="item roman-bold"><span class="label">vii.</span><div><b>Take Notes -</b> Lastly, write all this information in one place and save or tag emails in a way they can be easily found. If you don't you will quickly end up with a mountain of random sticky notes from calls, emails spread out over numerous places and half-finished DraftPad Docs or SlideCraft presentations.</div></div>
      </div>
    </div></div>
    <div class="item tight"><span class="label">b.</span><div>Although it is more work upfront to ask the right questions - it will be well worth your time and money. There is nothing worse than deciding on a venue, making a deposit, and then to only realize later that the parking options are a deal breaker or something you ‘thought you agreed to’ ended up being a miscommunication and now you're arguing about getting a deposit back and scrambling at the last minute to find a new venue.</div></div>
  </div>

  <p class="folio">7 Quiet Slip-Ups Party Hosts Overlook &nbsp;| <strong>5</strong></p>
  <svg class="corner" width="40" height="60" viewBox="0 0 40 60" aria-hidden="true">
    <path d="M40 12 Q18 18 12 60 L40 60 Z" fill="var(--brand-red)"/>
  </svg>
</section>

</body>
</html>
```